Wholesale in Gold Jewellery & Gold Bullion

We are an established gold jewellery and gold bullion wholesaler selling these products to international clients. We already have a name and logo of our company, hence please view attached current card design. We need a completely new design to compliment our business and industry and the final design should be new and elegant.

Contact Information for Business Card

New card details must be same as per current card. Like logo, name, tel no. & etc.

Colors

Designer to choose colors to be used in the design.

```html
<!DOCTYPE html>
<html lang="en">
<head>
<meta charset="utf-8">
<title>Meraval &amp; Co – Business Card</title>
<link href="https://fonts.googleapis.com/css2?family=Roboto+Slab:wght@600;700&family=PT+Sans:wght@400&display=swap" rel="stylesheet">
<style>
  :root {
    --stage: #cfcfcf;
    --card-dark: #43413d;
    --card-light: #ffffff;
    --gold: #d9960f;
    --ink: #4a4845;
    --text-light: #ffffff;
  }
  html, body {
    margin: 0;
    width: 1200px;
    height: 802px;
    overflow: hidden;
    background: var(--stage);
  }
  .canvas {
    position: relative;
    width: 1200px;
    height: 802px;
  }
  .card {
    position: absolute;
    top: 274px;
    width: 443px;
    height: 265px;
    overflow: hidden;
  }
  .card--front { left: 136px; background: var(--card-dark); }
  .card--back { left: 624px; background: var(--card-light); }

  .front-band {
    position: absolute;
    left: 0; top: 0;
    width: 75px; height: 100%;
    background: var(--gold);
  }
  .front-disc {
    position: absolute;
    left: -32px; top: 0;
    width: 265px; height: 265px;
    border-radius: 50%;
    background: var(--card-light);
  }

  .details {
    position: absolute;
    right: 27px;
    top: 60px;
    text-align: right;
    font-family: "PT Sans", sans-serif;
    color: var(--text-light);
    font-size: 12.5px;
    line-height: 15.5px;
  }
  .details__name {
    font-family: "Roboto Slab", serif;
    font-weight: 700;
    color: var(--gold);
    font-size: 13.5px;
    line-height: 15px;
    letter-spacing: 0.2px;
    margin: 0;
  }
  .details__role { margin: 0 0 11px; }
  .details__address { margin: 0 0 11px; }
  .contact-list { list-style: none; margin: 0; padding: 0; }
  .contact-list li {
    display: flex;
    justify-content: flex-end;
    align-items: center;
    gap: 3px;
  }
  .contact-list svg { width: 10px; height: 10px; fill: var(--gold); }

  .brand {
    position: absolute;
    left: 0; right: 0;
    top: 82px;
    display: flex;
    flex-direction: column;
    align-items: center;
  }
  .brand__dot {
    width: 62px; height: 62px;
    border-radius: 50%;
    background: var(--gold);
    margin-bottom: 12px;
  }
  .brand__name {
    font-family: "Roboto Slab", serif;
    font-weight: 600;
    font-size: 24px;
    letter-spacing: 0.5px;
    color: var(--ink);
    margin: 0;
  }
</style>
</head>
<body>
<main class="canvas">
  <section class="card card--front" aria-label="Card front">
    <div class="front-band"></div>
    <div class="front-disc"></div>
    <div class="details">
      <p class="details__name">ARJUN MERAVAL</p>
      <p class="details__role">Director</p>
      <p class="details__address">52 Lower Kent Rd<br>Singapore 218870</p>
      <ul class="contact-list">
        <li>+65 6120 4400
          <svg viewBox="0 0 10 10" aria-hidden="true"><path d="M1 3.5C1 2 3 1.5 5 1.5S9 2 9 3.5V4.5H7V3.6H3V4.5H1Z M2.5 5h5l1 3.5h-7z"/></svg>
        </li>
        <li>+65 9188 2536
          <svg viewBox="0 0 10 10" aria-hidden="true"><path d="M2.5 0.5h5v9h-5z M3.3 1.3v6.4h3.4V1.3z"/></svg>
        </li>
        <li>+65 6344 7201
          <svg viewBox="0 0 10 10" aria-hidden="true"><path d="M2.5 0.5h5v2.5h-5z M1 3.5h8v4H7.5v2h-5v-2H1z"/></svg>
        </li>
        <li>arjun@meravalco.com
          <svg viewBox="0 0 10 10" aria-hidden="true"><path d="M0.5 2h9v6.5h-9z" /><path d="M0.5 2l4.5 3.5L9.5 2" fill="none" stroke="#43413d" stroke-width="0.8"/></svg>
        </li>
      </ul>
    </div>
  </section>

  <section class="card card--back" aria-label="Card back">
    <div class="brand">
      <div class="brand__dot"></div>
      <p class="brand__name">MERAVAL &amp; CO</p>
    </div>
  </section>
</main>
</body>
</html>
```